Resposive web site in 4 languages + image gallery + logo design

We need a web page, which will work on all devices.
I have uploaded web page concept.
Company name: Praxelun
Industry/Entity Type
It Company
Logo Text
quality matters
Coding
Coded - Design and coding required
Number of Pages Required
1 page

```html
<!DOCTYPE html>
<html lang="en">
<head>
<meta charset="utf-8">
<title>Praxelun — Wood, Stone and Restoration</title>
<link href="https://fonts.googleapis.com/css2?family=Cinzel:wght@400;700&family=Lato:wght@400;700&display=swap" rel="stylesheet">
<style>
:root{
  --orange:#f7941d;
  --navy:#1c4b7b;
  --ink:#222;
  --text:#3a3a3a;
  --rule:#cfcfcf;
  --panel:#f1f1f1;
  --white:#fff;
}
*{box-sizing:border-box;margin:0;padding:0}
html,body{width:1200px;height:2535px;overflow:hidden;background:var(--white)}
body{position:relative;font-family:'Lato',sans-serif;color:var(--text)}
.abs{position:absolute}

/* top strip */
.topbar{left:0;top:0;width:1200px;height:37px;background:var(--orange)}
.tab{top:0;height:37px;background:var(--navy);color:var(--white);font-weight:700;font-size:17px;display:flex;align-items:center;gap:9px;padding:0 14px}
.tab.social{left:857px;width:146px}
.tab.lang{left:1006px;width:133px}
.tab .square{width:22px;height:22px;background:var(--white);border-radius:3px}
.tab .dot{width:16px;height:16px;border-radius:50%;background:var(--white)}

/* header */
.header{left:0;top:37px;width:1200px;height:78px;background:var(--white);border-bottom:1px solid #e4e4e4}
.brand{left:61px;top:20px;display:flex;align-items:center;gap:10px;font-family:'Cinzel',serif;font-weight:700;font-size:30px;color:var(--orange);letter-spacing:1px}
.brand .mark{width:26px;height:26px;background:var(--navy)}
.nav{top:30px;font-family:'Cinzel',serif;font-size:17px;color:var(--ink);letter-spacing:.5px;text-transform:uppercase}
.nav.active{color:var(--orange)}
.nav.active::after{content:"";position:absolute;left:-4px;right:-4px;top:28px;height:2px;background:var(--orange)}

/* hero */
.hero{left:0;top:115px;width:1200px;height:489px;background:linear-gradient(180deg,#1f3150 0%,#3a4a63 35%,#6c5a45 62%,#3b3a2a 82%,#232a1e 100%)}
.hero-title{left:0;top:338px;width:1200px;text-align:center;font-family:'Cinzel',serif;font-weight:400;font-size:40px;line-height:50px;color:var(--white);letter-spacing:1px;text-transform:uppercase;text-shadow:0 2px 6px rgba(0,0,0,.45)}
.quote-btn{left:493px;top:408px;width:211px;height:44px;border-radius:22px;background:var(--orange);border:3px solid var(--navy);display:flex;align-items:center;padding-left:8px;gap:14px;color:var(--white);font-weight:700;font-size:21px}
.quote-btn .ico{width:30px;height:30px;border-radius:50%;background:var(--white);border:3px solid var(--navy)}
.arrow{top:342px}

/* section titles */
.sec-title{left:0;width:1200px;text-align:center;font-family:'Cinzel',serif;font-weight:700;font-size:36px;line-height:44px;color:var(--ink);text-transform:uppercase}
.sec-title span{color:var(--orange);font-weight:400}
.sec-rule{left:333px;width:534px;height:1px;background:var(--rule)}
.sec-rule::after{content:"";position:absolute;left:200px;width:134px;top:-1px;height:3px;background:var(--navy)}

.welcome-text{left:66px;top:708px;width:1068px;text-align:center;font-size:14.5px;line-height:23px}
.read-more{left:546px;top:811px;width:107px;height:32px;background:var(--navy);color:var(--white);font-size:13px;display:flex;align-items:center;justify-content:center;border-radius:2px}

/* services */
.band-grey{left:0;width:1200px;background:var(--panel)}
.photo{border:1px solid #ddd}
.thumb{width:54px;height:54px;border:2px solid #fff;box-shadow:0 0 0 1px #ccc}
.thumb.on{box-shadow:0 0 0 2px var(--orange)}
.svc-head{font-size:25px;font-weight:400;color:var(--navy);letter-spacing:.3px}
.svc-text{font-size:15.5px;line-height:32px;letter-spacing:.3px}

/* quality band */
.quality{left:0;top:1995px;width:1200px;height:239px;background:linear-gradient(90deg,#1b4671,#245585 50%,#1b4671)}
.quality-line{left:0;width:1200px;text-align:center;color:var(--white);font-size:18.5px}
.quality-rule{left:393px;top:2150px;width:414px;height:1px;background:rgba(255,255,255,.3)}
.quality-tag{left:0;top:2168px;width:1200px;text-align:center;color:var(--orange);font-weight:700;font-size:18px}

/* footer */
.foot-head{top:2268px;font-family:'Cinzel',serif;font-size:20px;color:var(--ink);letter-spacing:.5px;padding-bottom:10px;border-bottom:2px solid var(--rule);text-transform:uppercase}
.qlink{left:61px;font-size:14px;color:var(--ink)}
.qlink::before{content:"›";color:var(--orange);margin-right:8px}
.qlink.on{color:var(--orange);font-weight:700}
.contact{font-size:14px;line-height:20px}
.contact b{color:var(--ink)}
.field{border:1px dashed #bbb;font-size:13px;color:var(--ink);padding:6px 10px}
.submit{left:877px;top:2424px;width:85px;height:33px;background:var(--orange);color:var(--white);font-weight:700;font-size:14px;display:flex;align-items:center;justify-content:center}
.copyright{left:0;top:2488px;width:1200px;height:47px;background:var(--navy);color:var(--white);font-size:14px;display:flex;align-items:center;justify-content:center}
</style>
</head>
<body>

<div class="abs topbar">
  <div class="abs tab social">Find Us On <span class="square"></span></div>
  <div class="abs tab lang"><span class="dot"></span>English
    <svg width="12" height="8" viewBox="0 0 12 8"><path d="M0 0h12L6 8z" fill="#fff"/></svg>
  </div>
</div>

<header class="abs header">
  <div class="abs brand"><span class="mark"></span>Praxelun</div>
  <div class="abs nav active" style="left:630px">Home</div>
  <div class="abs nav" style="left:744px">Services</div>
  <div class="abs nav" style="left:882px">About Us</div>
  <div class="abs nav" style="left:1028px">Contact Us</div>
</header>

<section class="abs hero" role="img" aria-label="Large stone house with lit windows at dusk, lawn in front"></section>
<svg class="abs arrow" style="left:38px" width="20" height="40" viewBox="0 0 20 40"><path d="M18 2L3 20l15 18" fill="none" stroke="#fff" stroke-width="2"/></svg>
<svg class="abs arrow" style="left:1142px" width="20" height="40" viewBox="0 0 20 40"><path d="M2 2l15 18L2 38" fill="none" stroke="#fff" stroke-width="2"/></svg>
<h1 class="abs hero-title">Are you interested in an estimate?</h1>
<div class="abs quote-btn"><span class="ico"></span>GET A QUOTE</div>

<h2 class="abs sec-title" style="top:636px">Welcome to <span>Praxelun</span></h2>
<div class="abs sec-rule" style="top:686px"></div>
<p class="abs welcome-text">Praxelun is a company whose business operations include making wooden products, restoration and building structures from natural stone. All of our products are made by craftsmen and specialists who have extensive experience and knowledge in their fields. The products we offer are always handmade and we take the requests and ideas of the specific client into account We always strive to achieve the best possible quality.</p>
<div class="abs read-more">READ MORE</div>

<div class="abs band-grey" style="top:888px;height:431px"></div>
<h2 class="abs sec-title" style="top:920px">Our <span>Services</span></h2>
<div class="abs sec-rule" style="top:971px"></div>

<div class="abs photo" style="left:61px;top:1028px;width:285px;height:235px;background:linear-gradient(135deg,#c9b596,#7a6246 55%,#2b2420)" role="img" aria-label="Wooden dining table with dark chairs"></div>
<div class="abs thumb" style="left:362px;top:1031px;background:#9a6a3c" role="img" aria-label="Wooden cabinet"></div>
<div class="abs thumb" style="left:362px;top:1090px;background:#4a3a2c" role="img" aria-label="Wooden furniture"></div>
<div class="abs thumb" style="left:362px;top:1149px;background:#7a4a2a" role="img" aria-label="Wooden door"></div>
<div class="abs thumb" style="left:362px;top:1208px;background:#c08a58" role="img" aria-label="Wood pieces"></div>
<h3 class="abs svc-head" style="left:463px;top:1020px">WOOD WORKS</h3>
<p class="abs svc-text" style="left:463px;top:1066px;width:680px">Timber is, in essence, a natural and warm material. Wood is also relatively durable and easy to work with, which has made it a favourite of builders throughout history. Our goal is to offer suitable products and quality furniture with installation and after-sales service to all of our clients. In order to achieve this, we' ready to help our clients in all stages of construction from design to production and maintenance</p>

<h3 class="abs svc-head" style="left:61px;top:1368px">STONE WORKS</h3>
<p class="abs svc-text" style="left:61px;top:1412px;width:695px">The natural stone found in the ground has been used in construction for centuries because of its durability. A structure built by a skilled craftsman from natural stone is unique, genuine and durable, and perfect for our bracing climate. Our experienced craftsmen are ready to help you in all stages of construction from planning to completion.</p>
<div class="abs photo" style="left:781px;top:1374px;width:287px;height:235px;background:linear-gradient(160deg,#d9d6cf,#a59b8b 50%,#5d6a48)" role="img" aria-label="Stone house with terrace wall and parasol"></div>
<div class="abs thumb" style="left:1083px;top:1375px;background:#a9a9a2" role="img" aria-label="Stone paving"></div>
<div class="abs thumb on" style="left:1083px;top:1435px;background:#9a9080" role="img" aria-label="Stone terrace"></div>
<div class="abs thumb" style="left:1083px;top:1495px;background:#6f7060" role="img" aria-label="Stone path"></div>
<div class="abs thumb" style="left:1083px;top:1555px;background:#3a3028" role="img" aria-label="Stone wall at night"></div>

<div class="abs band-grey" style="top:1657px;height:338px"></div>
<div class="abs photo" style="left:61px;top:1709px;width:285px;height:233px;background:linear-gradient(135deg,#e4ddd0,#a38b6c 55%,#5a4632)" role="img" aria-label="Restored dining room with rustic table and large wall clock"></div>
<div class="abs thumb" style="left:362px;top:1711px;background:#b89a6c" role="img" aria-label="Wooden beams"></div>
<div class="abs thumb" style="left:362px;top:1770px;background:#8a6c50" role="img" aria-label="Restored interior"></div>
<div class="abs thumb" style="left:362px;top:1829px;background:#5b5048" role="img" aria-label="Restored doorway"></div>
<div class="abs thumb" style="left:362px;top:1888px;background:#c88a3c" role="img" aria-label="Wooden staircase"></div>
<h3 class="abs svc-head" style="left:463px;top:1700px">RESTORATION</h3>
<p class="abs svc-text" style="left:463px;top:1746px;width:680px">It's good to see that fixing old things has become popular again in recent years and people are trying to find ways to preserve valuable old windows and pieces of furniture before deciding to replace them. It is possible to give a new life to almost any wooden door,window, piece of furniture or staircase. The extensive experience of our craftsmen will help you achieve the desired result.</p>

<section class="abs quality"></section>
<p class="abs quality-line" style="top:2045px">All of our products are made by craftsmen and specialists who have extensive experience and knowledge in their fields.</p>
<p class="abs quality-line" style="top:2076px">The products we offer are always handmade and we take the requests and ideas of the specific client into account</p>
<p class="abs quality-line" style="top:2106px">We always strive to achieve the best possible quality.</p>
<div class="abs quality-rule"></div>
<div class="abs quality-tag">QUALITY MATTERS, PRAXELUN</div>

<div class="abs foot-head" style="left:61px;width:148px">Quick Links</div>
<div class="abs foot-head" style="left:286px;width:250px">Contact Details</div>
<div class="abs foot-head" style="left:610px;width:530px">Quick Inquiry</div>

<div class="abs qlink on" style="top:2322px">Home</div>
<div class="abs qlink" style="top:2360px">Services</div>
<div class="abs qlink" style="top:2399px">About Us</div>
<div class="abs qlink" style="top:2438px">Contact Us</div>

<svg class="abs" style="left:288px;top:2324px" width="16" height="22" viewBox="0 0 16 22"><path d="M8 0a8 8 0 0 0-8 8c0 6 8 14 8 14s8-8 8-14a8 8 0 0 0-8-8z" fill="#f7941d"/><circle cx="8" cy="8" r="3" fill="#fff"/></svg>
<div class="abs contact" style="left:318px;top:2320px"><b>PRAXELUN</b><br>Kaskede 12, 10115 Harjuvald<br>Estonia</div>
<svg class="abs" style="left:288px;top:2400px" width="16" height="16" viewBox="0 0 16 16"><path d="M3 1l3 3-2 2c1 2 3 4 5 5l2-2 3 3-2 3C6 15 1 10 1 3z" fill="#f7941d"/></svg>
<div class="abs contact" style="left:318px;top:2398px">555-014-2290</div>
<svg class="abs" style="left:288px;top:2441px" width="16" height="12" viewBox="0 0 16 12"><rect width="16" height="12" rx="1" fill="#f7941d"/><path d="M1 1l7 6 7-6" fill="none" stroke="#fff" stroke-width="1.3"/></svg>
<div class="abs contact" style="left:318px;top:2437px">sales@praxelun.example</div>

<div class="abs field" style="left:614px;top:2326px;width:250px;height:34px">Name</div>
<div class="abs field" style="left:614px;top:2373px;width:250px;height:34px">Phone</div>
<div class="abs field" style="left:614px;top:2422px;width:250px;height:34px">Email</div>
<div class="abs field" style="left:877px;top:2326px;width:262px;height:81px">Message</div>
<div class="abs submit">SUBMIT</div>

<footer class="abs copyright">COPYRIGHT © 2016 PRAXELUN. ALL RIGHTS RESERVED.</footer>

</body>
</html>
```